Real Estate Website

I am looking for a website design for a website that will be featuring real estate listings across Australia. It will be a website for a real estate agency that operates through all states in Australia.

We like the designs of https://www.brightnest.com.au/ and https://valtoria.example/

On the brightnest website, we like the sell, buy, sold tabs but would also like lease, and agents. We also need a button somewhere for 'Join Agent Pivola' and 'Login'

On the Valtoria site it has a concierge section and we want something like that on the home page.

The contact details to show in the footer are:

Shop 2217B
Level 1 Harbourgate Shopping Centre
87 Quillon Terrace
Southport

Attached are various versions of the logo and some intro text to go on the home page.

```html
<!DOCTYPE html>
<html lang="en">
<head>
<meta charset="utf-8">
<title>Agent Pivola — Real Estate</title>
<link rel="stylesheet" href="https://fonts.googleapis.com/css2?family=Arimo:ital,wght@0,400;0,600;0,700;1,700&display=swap">
<style>
:root{
  --gold:#b0843c;
  --gold-light:#cdae66;
  --gold-dark:#9a6a2a;
  --ink:#222222;
  --body:#555555;
  --muted:#888888;
  --paper:#ffffff;
  --cream:#f8f6f3;
  --footer:#2b2b2b;
  --line:#e2e2e2;
}
*{box-sizing:border-box;margin:0;padding:0}
html,body{width:1200px;height:4217px;overflow:hidden}
body{font-family:"Arimo",Arial,sans-serif;color:var(--ink);background:var(--paper);position:relative}
.abs{position:absolute}
.btn{position:absolute;display:flex;align-items:center;justify-content:center;border-radius:30px;font-weight:700;font-size:14px;letter-spacing:.3px;text-transform:uppercase}
.btn-gold{background:linear-gradient(90deg,var(--gold-dark),var(--gold-light));color:#fff}
.btn-outline{border:1.5px solid var(--gold);color:var(--ink);background:#fff}
.title{position:absolute;left:0;width:1200px;text-align:center;font-weight:700;font-size:40px;text-transform:uppercase}
.title::after{content:"";display:block;width:82px;height:3px;background:var(--gold);margin:10px auto 0}
.photo{position:absolute}

/* hero */
.hero{position:absolute;left:0;top:0;width:1200px;height:643px;background:linear-gradient(180deg,#d6e4ee 0%,#b9cfe0 35%,#6f9ab6 55%,#2b6f96 75%,#1f5d82 100%)}
.nav a{position:absolute;top:59px;font-size:14px;font-weight:700;color:var(--ink);text-decoration:none}
.nav a.active{color:var(--gold);border-bottom:2px solid var(--gold)}
.brand-name{position:absolute;left:500px;top:56px;width:200px;text-align:center;font-size:20px;font-weight:700;color:var(--ink)}
.hero .kicker{top:236px;font-size:21px;font-style:italic;font-weight:700;color:var(--gold);left:0;width:1200px;text-align:center}
.hero h1{position:absolute;top:275px;left:0;width:1200px;text-align:center;font-size:52px;font-weight:700}
.hero h2{position:absolute;top:340px;left:0;width:1200px;text-align:center;font-size:37px;font-weight:400}
.dots{position:absolute;display:flex;gap:8px}
.dots i{width:11px;height:11px;border-radius:50%;border:1.5px solid #fff;display:block}
.dots i.on{background:#fff}

/* browse */
.browse{position:absolute;left:0;top:643px;width:1200px;height:334px;background:linear-gradient(90deg,var(--gold-dark),var(--gold-light))}
.browse h3{position:absolute;top:50px;left:0;width:1200px;text-align:center;color:#fff;font-size:40px;font-weight:700}
.browse h3::after{content:"";display:block;width:82px;height:3px;background:#fff;margin:8px auto 0}
.search-box{position:absolute;left:214px;top:158px;width:772px;height:120px;border:1.5px solid rgba(255,255,255,.8);border-radius:12px}
.tab{position:absolute;top:134px;height:48px;border-radius:26px;border:1.5px solid #fff;color:#fff;font-size:14px;font-weight:700;display:flex;align-items:center;justify-content:center;width:92px}
.tab.on{background:#fff;color:var(--ink)}
.field{position:absolute;left:246px;top:204px;width:556px;height:48px;background:#fff;border-radius:26px;font-size:15px;padding-left:24px;display:flex;align-items:center}
.go{position:absolute;left:812px;top:204px;width:142px;height:48px;background:#262626;color:#fff;border-radius:26px;font-size:14px;font-weight:700;display:flex;align-items:center;justify-content:center}

/* about */
.about-kicker{left:556px;top:1122px;color:var(--gold);font-style:italic;font-weight:700;font-size:17px}
.about h4{position:absolute;left:556px;top:1162px;border-left:3px solid var(--gold);padding-left:22px;font-size:27px;font-weight:700;line-height:38px;width:560px}
.about p{position:absolute;left:556px;width:534px;font-size:13.5px;line-height:23px;color:var(--body);text-align:justify}

/* tiles */
.tile{position:absolute;top:1673px;width:297px;height:360px}
.tile .pill{position:absolute;left:80px;top:264px;width:137px;height:54px;border-radius:30px;background:#fff;font-size:24px;font-weight:700;display:flex;align-items:center;justify-content:center}
.tile .pill.gold{background:linear-gradient(90deg,var(--gold-dark),var(--gold-light));color:#fff}

/* cards */
.card{position:absolute;top:2230px;width:303px;height:422px;background:#fff;box-shadow:0 2px 12px rgba(0,0,0,.12)}
.card .img{position:absolute;left:7px;top:7px;width:289px;height:218px}
.card h5{position:absolute;left:22px;top:248px;font-size:18px;font-weight:400}
.card p{position:absolute;left:22px;top:280px;width:260px;font-size:13.5px;line-height:23px;color:var(--body)}
.card .meta{position:absolute;left:22px;top:332px;font-size:12px;font-weight:700}
.card .btn{left:22px;top:360px;width:150px;height:48px;font-size:14px}
.card .price{position:absolute;right:28px;top:376px;font-size:17px;font-weight:700;color:var(--gold)}

/* concierge */
.concierge{position:absolute;left:0;top:2750px;width:1200px;height:553px;background:var(--cream)}
.concierge .lead{position:absolute;top:168px;left:0;width:1200px;text-align:center;font-weight:700;font-size:17px;line-height:29px}
.concierge .txt{position:absolute;top:234px;left:190px;width:820px;text-align:center;font-size:15px;line-height:24px}

/* testimonials */
.quote{position:absolute;top:3487px;width:305px;height:273px;background:#fff;box-shadow:0 2px 12px rgba(0,0,0,.12)}
.stars{position:absolute;left:24px;top:22px;color:var(--gold);font-size:15px;letter-spacing:1px}
.quote p{position:absolute;left:24px;top:52px;width:258px;font-size:13px;line-height:21px;color:var(--body);text-align:justify}
.quote hr{position:absolute;left:24px;top:168px;width:258px;border:0;border-top:1px solid var(--line)}
.avatar{position:absolute;left:24px;top:188px;width:54px;height:54px;border-radius:50%;background:linear-gradient(135deg,#d9c8b8,#8c7a6c)}
.quote b{position:absolute;left:100px;top:198px;font-size:13px}
.quote small{position:absolute;left:100px;top:219px;font-size:12px;color:var(--muted)}

/* footer */
.footer{position:absolute;left:0;top:3876px;width:1200px;height:341px;background:var(--footer);color:#fff}
.footer h6{position:absolute;top:56px;font-size:18px;font-weight:700}
.footer .link{position:absolute;font-size:14px}
.footer .link::before{content:"»";color:var(--gold);margin-right:18px}
.footer-name{position:absolute;left:111px;top:130px;width:220px;text-align:center;font-size:24px;font-weight:700;color:#fff}
.ficon{position:absolute;left:818px;width:38px;height:38px;border-radius:50%;background:#fff;display:flex;align-items:center;justify-content:center}
.ftext{position:absolute;left:873px;font-size:14px;line-height:20px}
.soc{position:absolute;top:302px;width:34px;height:34px;border-radius:50%;border:1.5px solid #777}
</style>
</head>
<body>

<!-- hero -->
<header class="hero">
  <div class="photo" role="img" aria-label="Harbour city skyline with waterfront opera building" style="left:0;top:0;width:1200px;height:643px;background:linear-gradient(180deg,rgba(232,240,246,.9) 0%,rgba(180,205,222,.6) 40%,rgba(40,110,150,.8) 70%,#1d5a7f 100%)"></div>
  <nav class="nav">
    <a class="active" style="left:110px">HOME</a>
    <a style="left:175px">SELL</a>
    <a style="left:232px">BUY</a>
    <a style="left:283px">AGENTS</a>
    <a style="left:362px">ABOUT</a>
    <a style="left:434px">CONTACT</a>
  </nav>
  <div class="brand-name">Agent Pivola</div>
  <div class="btn" style="left:763px;top:42px;width:197px;height:48px;background:#fff;color:var(--ink);font-size:13.5px">JOIN AGENT PIVOLA</div>
  <div class="btn btn-gold" style="left:969px;top:42px;width:119px;height:48px;font-size:13.5px">
    <svg width="12" height="12" viewBox="0 0 12 12" style="margin-right:6px"><circle cx="6" cy="3.5" r="3" fill="#fff"/><path d="M0 12c0-4 2.5-5.5 6-5.5S12 8 12 12z" fill="#fff"/></svg>LOGIN</div>
  <div class="abs kicker">WELCOME TO AGENT PIVOLA</div>
  <h1>FIND YOUR DREAM HOME.</h1>
  <h2>FAST, SMART, CENTRALIZED</h2>
  <div class="btn btn-gold" style="left:493px;top:398px;width:214px;height:46px;font-size:14px">LIST YOUR PROPERTY</div>
  <div class="dots" style="left:563px;top:597px"><i></i><i class="on"></i><i></i><i></i></div>
</header>

<!-- browse -->
<section class="browse">
  <h3>BROWSE PROPERTIES</h3>
  <div class="search-box"></div>
  <div class="tab on" style="left:403px">SELL</div>
  <svg class="abs" style="left:440px;top:180px" width="16" height="10"><path d="M0 0h16L8 9z" fill="#fff"/></svg>
  <div class="tab" style="left:504px">BUY</div>
  <div class="tab" style="left:604px">SOLD</div>
  <div class="tab" style="left:705px">LEASE</div>
  <div class="field">Start typing to find your address</div>
  <div class="go">SEARCH</div>
</section>

<!-- about -->
<section class="about">
  <div class="abs" style="left:140px;top:1090px;width:326px;height:408px;border:1.5px solid var(--gold)"></div>
  <div class="photo" role="img" aria-label="Agent reviewing plans in front of a family house" style="left:120px;top:1074px;width:325px;height:408px;background:linear-gradient(160deg,#c9d4dc,#8a9488 60%,#5b6b4e)"></div>
  <div class="photo" role="img" aria-label="Modern white villa with pool at dusk" style="left:280px;top:1327px;width:220px;height:249px;background:linear-gradient(180deg,#9bb7d6,#e4e6ea 55%,#8fb9c8);border:3px solid #fff"></div>
  <div class="abs about-kicker">WHO WE ARE</div>
  <h4>REAL ESTATE MADE SIMPLE,<br>SMART, AND CENTRAL</h4>
  <p style="top:1256px">Lorem ipsum dolor sit amet, consectetur adipiscing elit, sed do eiusmod tempor incididunt ut labore et dolore magna aliqua. Ut enim ad minim veniam, quis nostrud exercitation ullamco laboris nisi ut aliquip ex ea commodo consequat. Duis aute irure dolor in reprehenderit in voluptate velit esse cillum dolore eu fugiat nulla pariatur. Excepteur sint occaecat cupidatat non proident, sunt in culpa qui officia deserunt mollit anim id est laborum.</p>
  <p style="top:1406px">Lorem ipsum dolor sit amet, consectetur adipiscing elit, sed do eiusmod tempor incididunt ut labore et dolore magna aliqua.</p>
  <div class="btn btn-outline" style="left:556px;top:1479px;width:150px;height:48px;font-size:14px">LEARN MORE</div>
</section>

<!-- tiles -->
<div class="tile" style="left:0"><div class="photo" role="img" aria-label="Dark grey house with lawn" style="inset:0;background:linear-gradient(180deg,#6f9acb,#5a6a5e 45%,#6c9a4a)"></div><div class="pill">SELL</div></div>
<div class="tile" style="left:301px"><div class="photo" role="img" aria-label="Two-storey suburban home" style="inset:0;background:linear-gradient(180deg,#bcd0e4,#8a8276 50%,#7fa560)"></div><div class="pill">BUY</div></div>
<div class="tile" style="left:602px"><div class="photo" role="img" aria-label="Couple shaking hands with an agent in a bright apartment" style="inset:0;background:linear-gradient(160deg,#e9ecef,#b7bcc2 50%,#6b7078)"></div><div class="pill gold">SOLD</div></div>
<div class="tile" style="left:903px"><div class="photo" role="img" aria-label="Tenants reviewing a lease with an agent" style="inset:0;background:linear-gradient(160deg,#ece9e4,#c1b6a8 50%,#5d6a78)"></div><div class="pill">LEASE</div></div>
<div class="dots" style="left:586px;top:2066px;gap:4px"><i style="border:0;background:#e3d3b8"></i><i style="border:0;background:var(--gold)"></i></div>

<!-- featured -->
<h2 class="title" style="top:2138px">FEATURED LISTINGS</h2>
<svg class="abs" style="left:64px;top:2428px" width="16" height="24"><path d="M12 2 3 12l9 10" stroke="#aaa" stroke-width="2.5" fill="none"/></svg>
<svg class="abs" style="left:1118px;top:2428px" width="16" height="24"><path d="M4 2l9 10-9 10" stroke="#222" stroke-width="2.5" fill="none"/></svg>

<article class="card" style="left:124px">
  <div class="img" role="img" aria-label="White apartment building" style="background:linear-gradient(180deg,#a9c7e6,#e6e4df 55%,#8c8c86)"></div>
  <h5>LOREM IPSUM DOLOR</h5>
  <p>Lorem ipsum dolor sit amet, consectetu adipiscing elit, sed.</p>
  <div class="meta">3 beds &nbsp;•&nbsp; 2 baths &nbsp;•&nbsp; 1,334 sqft</div>
  <div class="btn btn-outline">VIEW DETAILS</div><div class="price">$425,000</div>
</article>
<article class="card" style="left:449px">
  <div class="img" role="img" aria-label="Modern home with garage and paved drive" style="background:linear-gradient(180deg,#c8a9d6,#d9d5d0 50%,#8a9a7a)"></div>
  <h5>LOREM IPSUM DOLOR</h5>
  <p>Lorem ipsum dolor sit amet, consectetu adipiscing elit, sed.</p>
  <div class="meta">3 beds &nbsp;•&nbsp; 2 baths &nbsp;•&nbsp; 1,334 sqft</div>
  <div class="btn btn-gold">VIEW DETAILS</div><div class="price">$425,000</div>
</article>
<article class="card" style="left:773px">
  <div class="img" role="img" aria-label="Row of townhouses with trees" style="background:linear-gradient(180deg,#7eaee0,#b9b6ad 50%,#6f9a4a)"></div>
  <h5>LOREM IPSUM DOLOR</h5>
  <p>Lorem ipsum dolor sit amet, consectetu adipiscing elit, sed.</p>
  <div class="meta">3 beds &nbsp;•&nbsp; 2 baths &nbsp;•&nbsp; 1,334 sqft</div>
  <div class="btn btn-outline">VIEW DETAILS</div><div class="price">$425,000</div>
</article>

<!-- concierge -->
<section class="concierge">
  <div class="photo" role="img" aria-label="Row of new white houses with dark roofs" style="left:0;top:280px;width:1200px;height:273px;background:linear-gradient(180deg,rgba(248,246,243,0),#dcdad5 35%,#8b8f88 70%,#4f6a3c)"></div>
  <h2 class="title" style="top:74px">AGENT PIVOLA CONCIERGE</h2>
  <div class="lead">LOOKING BUY, RENT OR SELL SOMETHING UNIQUE? WANT COMPETITIVE<br>DEVELOPER FINANCING AT GREAT RATES?</div>
  <div class="txt">Concierge can help you find, buy, rent or sell unique properties through our extensive global agent network and assist with financing at competitive rates with fast approvals.</div>
  <div class="btn btn-gold" style="left:525px;top:300px;width:150px;height:46px;font-size:14px">LEARN MORE</div>
</section>

<!-- testimonials -->
<h2 class="title" style="top:3393px">TESTIMONIALS</h2>
<div class="quote" style="left:111px"><div class="stars">★★★★★</div><p>Lorem ipsum dolor sit amet, cons ectetur adipiscing elit, sed do eius mod tempor incididunt ut labore et dolore magna aliqua. Ut enim ad minim veniamea quis nostrud exercitationea.</p><hr><div class="avatar" role="img" aria-label="Client portrait"></div><b>MARCUS HALE</b><small>United States</small></div>
<div class="quote" style="left:447px"><div class="stars">★★★★★</div><p>Lorem ipsum dolor sit amet, cons ectetur adipiscing elit, sed do eius mod tempor incididunt ut labore et dolore magna aliqua. Ut enim ad minim veniamea quis nostrud exercitationea.</p><hr><div class="avatar" role="img" aria-label="Client portrait"></div><b>OLIVIA GRANT</b><small>United States</small></div>
<div class="quote" style="left:783px"><div class="stars">★★★★★</div><p>Lorem ipsum dolor sit amet, cons ectetur adipiscing elit, sed do eius mod tempor incididunt ut labore et dolore magna aliqua. Ut enim ad minim veniamea quis nostrud exercitationea.</p><hr><div class="avatar" role="img" aria-label="Client portrait"></div><b>MARCUS HALE</b><small>United States</small></div>
<div class="dots" style="left:569px;top:3797px;gap:12px"><i style="width:6px;height:6px;border:0;background:#ccc"></i><i style="width:6px;height:6px;border:0;background:var(--gold)"></i><i style="width:6px;height:6px;border:0;background:#ccc"></i><i style="width:6px;height:6px;border:0;background:#ccc"></i></div>

<!-- footer -->
<footer class="footer">
  <div class="footer-name">Agent Pivola</div>
  <h6 style="left:397px">QUICK LINKS</h6>
  <div class="link" style="left:397px;top:101px">Home</div>
  <div class="link" style="left:397px;top:137px">Sell</div>
  <div class="link" style="left:397px;top:173px">Buy</div>
  <div class="link" style="left:397px;top:209px">About</div>
  <div class="link" style="left:397px;top:245px">Agents</div>
  <div class="link" style="left:566px;top:101px">Site Map</div>
  <div class="link" style="left:566px;top:137px">Terms and Conditions</div>
  <div class="link" style="left:566px;top:173px">Privacy Policy</div>
  <div class="link" style="left:566px;top:209px">Contact Us</div>
  <h6 style="left:818px">CONTACT US</h6>
  <div class="ficon" style="top:99px"><svg width="14" height="18" viewBox="0 0 14 18"><path d="M7 0a7 7 0 0 0-7 7c0 5 7 11 7 11s7-6 7-11a7 7 0 0 0-7-7z" fill="var(--gold)"/><circle cx="7" cy="7" r="2.5" fill="#fff"/></svg></div>
  <div class="ftext" style="top:101px">Shop 2217B Level 1 Harbourgate<br>Shopping Centre 87 Quillon Terrace<br>Southport</div>
  <div class="ficon" style="top:164px"><svg width="16" height="16" viewBox="0 0 16 16"><path d="M3 1l3 3-1.5 2a9 9 0 0 0 5.5 5.5L12 10l3 3-2 2C7 15 1 9 1 3z" fill="var(--gold)"/></svg></div>
  <div class="ftext" style="top:173px">+61 7 5550 0142</div>
  <div class="ficon" style="top:215px"><svg width="16" height="12" viewBox="0 0 16 12"><rect width="16" height="12" rx="1.5" fill="var(--gold)"/><path d="M1 1l7 5 7-5" stroke="#fff" stroke-width="1.4" fill="none"/></svg></div>
  <div class="ftext" style="top:224px">info@agentpivola.com</div>
  <div class="abs" style="left:111px;top:283px;width:978px;border-top:1px solid #444"></div>
  <div class="abs" style="left:0;top:312px;width:1200px;text-align:center;font-size:12px">© 2025 AGENT PIVOLA - ALL RIGHTS RESERVED</div>
  <div class="soc" style="left:934px;background:var(--gold);border-color:var(--gold)"></div>
  <div class="soc" style="left:974px"></div>
  <div class="soc" style="left:1014px"></div>
  <div class="soc" style="left:1054px"></div>
</footer>

</body>
</html>
```